Lumora Systems New Website - IT Infrastructure | Smart Cabinet | Micro Data Center

We're an IT SI providing Server Room Design & Build | All-in-One Rack & Smart Cabinet | Structured Cabling | IT Relocation | Maintenance. Old website can be found at www.lumorasys.com.hk. We'd like a brand new wix website which is modern, minimalist, interactive with some animation. Website content will be mostly static and include our service, our project, news and events, about us, contacts, blogs, partners and brands, etc.

reference sites:
We'd like to see more designs referring to below

https://www.pixelvane.example/design/41736205
https://www.pixelvane.example/design/41892417
https://velbrinn.example/

Animation (scrolling effect) referring to
https://velbrinn.example/intelligence/smart-office-room/
Updates

we'd like below style.

Designs look the same

Target Market(s)

Commercials in HK

Industry/Entity Type

IT, Technology, Data Center

Coding

Coded - Design and coding required

Font styles to use
Sans Serif

Requirements
Must have
• CMS, Some Interactive Elements/ Graphics

```html
<!DOCTYPE html>
<html lang="en">
<head>
<meta charset="utf-8">
<title>Lumora Systems – IT Infrastructure</title>
<link href="https://fonts.googleapis.com/css2?family=Righteous&family=Poppins:wght@300;400;500;600;700&display=swap" rel="stylesheet">
<style>
:root{
  --red:#b3171b;
  --red-dark:#8f1014;
  --navy:#132c5e;
  --navy-deep:#0b1a3a;
  --ink:#1b1b1f;
  --muted:#4a4a52;
  --paper:#ffffff;
  --mist:#eef0f6;
  --card:#f1f1f1;
  --field:#e9ebf3;
}
*{box-sizing:border-box;margin:0;padding:0}
html,body{width:1200px;height:4886px;overflow:hidden}
body{position:relative;background:var(--paper);font-family:"Poppins",sans-serif;color:var(--ink)}
.display{font-family:"Righteous",sans-serif;font-weight:400}
section,header,footer{position:absolute;left:0;width:1200px}
.abs{position:absolute}
.btn{position:absolute;display:flex;align-items:center;justify-content:center;gap:6px;background:var(--red);color:#fff;font-family:"Righteous",sans-serif;font-size:12px;letter-spacing:.3px;text-transform:uppercase;clip-path:polygon(0 0,100% 0,100% 100%,14px 100%,0 calc(100% - 14px))}
.btn.outline{background:var(--red);box-shadow:inset 0 0 0 2px #fff}
.btn svg{width:11px;height:11px}

/* header */
.site-header{top:0;height:64px;z-index:3}
.brand{position:absolute;display:flex;align-items:center;gap:10px}
.brand-square{width:30px;height:30px;border:3px solid var(--ink);border-radius:3px}
.brand-name{font-family:"Righteous",sans-serif;font-size:30px;color:var(--ink)}
.nav{position:absolute;top:24px;left:0;font-family:"Righteous",sans-serif;font-size:13px;color:#333}
.nav a{position:absolute;white-space:nowrap;text-decoration:none;color:#333}
.nav a.active{color:var(--red)}
.login{top:13px;left:978px;width:118px;height:40px;font-size:11px}

/* hero */
.hero{top:0;height:760px}
.hero-media{position:absolute;left:0;top:64px;width:1200px;height:645px;
 background:
  radial-gradient(ellipse 360px 80px at 430px 210px,rgba(255,170,60,.55),transparent 70%),
  radial-gradient(ellipse 520px 90px at 880px 520px,rgba(255,120,40,.5),transparent 70%),
  radial-gradient(ellipse 300px 300px at 780px 300px,rgba(40,90,160,.55),transparent 70%),
  linear-gradient(120deg,#091530 0%,#122a55 45%,#0d1d40 100%)}
.hero-cabinets{position:absolute;left:590px;top:140px;width:330px;height:500px;background:linear-gradient(90deg,#1b3a72,#2b5599 50%,#17305e);opacity:.85;clip-path:polygon(8% 6%,100% 0,100% 92%,8% 100%)}
.hero-cut{position:absolute;left:0;top:60px}
.hero-copy{position:absolute;left:104px;top:236px;width:340px;color:#fff}
.hero-kicker{font-family:"Righteous",sans-serif;font-size:18px;color:var(--red)}
.hero-title{font-family:"Righteous",sans-serif;font-size:50px;line-height:58px;margin-top:8px}
.hero-title .accent{color:var(--red)}
.hero-text{font-size:10.5px;line-height:17px;margin-top:14px;width:330px}
.hero-btn{left:104px;top:485px;width:174px;height:45px}
.dots{position:absolute;left:1138px;top:346px;display:flex;flex-direction:column;gap:9px}
.dots i{display:block;width:13px;height:13px;border-radius:50%;background:#fff}
.dots i:first-child{background:var(--red)}
.hero-edge{position:absolute;left:0;top:640px}
.scroll-cue{position:absolute;left:578px;top:693px;width:44px;height:44px;border-radius:50%;background:#fff;box-shadow:0 3px 10px rgba(0,0,0,.25);display:flex;align-items:center;justify-content:center}

/* about */
.about{top:800px;height:440px}
.about-photo{position:absolute;left:87px;top:19px;width:398px;height:400px}
.about-photo .frame{position:absolute;left:100px;top:90px;width:298px;height:310px;border:2px solid var(--red);border-radius:0 0 18px 0}
.about-photo .shot{position:absolute;left:0;top:0;width:300px;height:300px;background:linear-gradient(135deg,#0f2a55,#2d6aa8 55%,#16375f);border:2px solid var(--red);border-radius:14px 0 0 0}
.about-photo .sq{position:absolute;width:26px;height:26px;background:var(--red);border-radius:3px}
.divider-v{position:absolute;left:546px;top:24px;width:1px;height:390px;background:#d0d0d6}
.about-title{position:absolute;left:622px;top:20px;font-family:"Righteous",sans-serif;font-size:34px;line-height:42px}
.about-text{position:absolute;left:622px;top:112px;width:480px;font-size:12.4px;line-height:22.3px;color:var(--muted)}
.about-btn{left:622px;top:330px;width:150px;height:45px}

/* services */
.services{top:1285px;height:602px}
.services-bg{position:absolute;inset:0;background:radial-gradient(ellipse 600px 300px at 300px 200px,rgba(60,110,190,.35),transparent 70%),linear-gradient(160deg,#10285a,#0c1d45);clip-path:polygon(0 100px,140px 0,100% 0,100% 470px,1060px 100%,0 100%)}
.section-title{position:absolute;left:0;width:1200px;text-align:center;font-family:"Righteous",sans-serif;font-size:34px}
.services .section-title{top:62px;color:#fff}
.svc{position:absolute;top:173px;width:249px;height:262px;background:linear-gradient(180deg,#3a4d6d,#1d2b44)}
.svc::after{content:"";position:absolute;inset:0;background:linear-gradient(180deg,transparent 45%,rgba(0,0,0,.65))}
.svc h3{position:absolute;left:16px;bottom:18px;z-index:1;font-family:"Righteous",sans-serif;font-size:17px;line-height:23px;color:#fff}
.svc.active{height:320px;background:var(--red)}
.svc.active::after{display:none}
.svc.active h3{position:absolute;top:48px;bottom:auto}
.svc.active p{position:absolute;left:16px;top:112px;width:222px;font-size:11px;line-height:21.5px;color:#fff}
.svc.active .btn{left:14px;top:260px;width:150px;height:44px;background:#fff;color:var(--red)}

/* projects */
.projects{top:1960px;height:560px}
.projects h2{position:absolute;left:104px;top:0;font-family:"Righteous",sans-serif;font-size:34px}
.projects .intro{position:absolute;left:104px;top:52px;width:440px;font-size:12px;line-height:20px;color:var(--muted)}
.projects .btn{left:104px;top:135px;width:158px;height:44px}
.proj{position:absolute;background:linear-gradient(160deg,#2c4f8a,#13264b)}
.proj::after{content:"";position:absolute;inset:0;background:linear-gradient(180deg,transparent 50%,rgba(0,0,0,.7))}
.proj h3{position:absolute;left:14px;bottom:14px;z-index:1;font-family:"Righteous",sans-serif;font-size:16px;line-height:23px;color:#fff}
.proj.wide h3{left:24px;bottom:26px}

/* partners */
.partners{top:2590px;height:292px;background:var(--mist)}
.partners .section-title{top:76px}
.badge{position:absolute;top:168px;width:188px;height:67px;background:#fff;display:flex;align-items:center;justify-content:center}
.badge span{display:block;width:110px;height:18px;border-radius:9px;background:#c9ccd4}
.badge.dark span{background:#3a3a40}
.badge.focus{box-shadow:0 0 0 2px #cfd3dc,0 4px 12px rgba(0,0,0,.12)}
.badge.focus span{background:#2b9c6a}

/* news */
.news{top:2929px;height:474px}
.news-bg{position:absolute;inset:0;background:radial-gradient(ellipse 500px 200px at 800px 120px,rgba(220,70,60,.4),transparent 70%),linear-gradient(135deg,#a8161a,#c32220 60%,#9a1317);clip-path:polygon(0 86px,200px 0,100% 0,100% 100%,0 100%)}
.news .section-title{top:78px;color:#fff}
.news-card{position:absolute;top:173px;width:476px;height:157px;background:#fff;border-radius:4px}
.news-card .thumb{position:absolute;left:3px;top:3px;width:144px;height:151px;background:linear-gradient(160deg,#4b6a94,#1e2f4c)}
.news-card h3{position:absolute;left:164px;top:22px;font-family:"Righteous",sans-serif;font-size:18px}
.meta{position:absolute;left:164px;top:58px;display:flex;gap:16px;font-size:11px;font-weight:600}
.meta span{display:flex;align-items:center;gap:4px}
.meta svg{width:11px;height:11px}
.news-card p{position:absolute;left:164px;top:80px;width:290px;font-size:11px;line-height:20px;color:var(--muted)}
.pager{position:absolute;left:576px;top:372px;display:flex;gap:9px}
.pager i{width:12px;height:12px;border-radius:50%;border:2px solid #fff}
.pager i:first-child{background:#fff}

/* blogs */
.blogs{top:3460px;height:490px}
.blogs .section-title{top:10px}
.blog{position:absolute;top:99px;width:317px;height:378px;background:var(--card)}
.blog .cover{height:205px}
.blog h3{position:absolute;left:22px;top:238px;font-family:"Righteous",sans-serif;font-size:19px}
.blog p{position:absolute;left:22px;top:268px;width:275px;font-size:11.2px;line-height:22px;color:var(--muted)}
.blog a{position:absolute;left:22px;top:338px;font-size:12px;font-weight:600;color:var(--red);text-decoration:underline}

/* contacts */
.contacts{top:4010px;height:512px}
.contacts-bg{position:absolute;inset:0;background:repeating-linear-gradient(90deg,rgba(255,255,255,.025) 0 40px,transparent 40px 80px),linear-gradient(180deg,#0d1a38,#111f42)}
.contacts .section-title{top:90px;color:#fff}
.field{position:absolute;left:135px;width:419px;height:46px;background:var(--field);border-radius:14px;font-size:13px;color:#444;padding:13px 20px}
.field.msg{left:567px;top:169px;height:174px}
.contacts .btn{left:535px;top:377px;width:129px;height:44px;font-size:12px}

/* footer */
.site-footer{top:4550px;height:336px}
.col-title{position:absolute;font-family:"Righteous",sans-serif;font-size:19px}
.links{position:absolute;list-style:none;font-size:12.5px;color:#444}
.links li{height:30px}
.links li.active{color:var(--red)}
.social{position:absolute;top:132px;width:26px;height:26px;border-radius:50%;background:var(--red)}
.contact-row{position:absolute;left:798px;display:flex;gap:22px;font-size:12.5px;line-height:22px;color:#444;width:300px}
.contact-row .ic{flex:none;width:26px;height:26px;border-radius:50%;background:var(--red);display:flex;align-items:center;justify-content:center}
.contact-row .ic svg{width:13px;height:13px}
.rule{position:absolute;left:104px;top:279px;width:992px;height:1px;background:#c9c9cf}
.copy{position:absolute;left:0;top:300px;width:1200px;text-align:center;font-size:11px;color:#444}
</style>
</head>
<body>

<section class="hero">
  <div class="hero-media" role="img" aria-label="Server cabinets in a dark blue room with orange light trails sweeping across">
    <div class="hero-cabinets"></div>
  </div>
  <svg class="hero-cut" width="1200" height="40" viewBox="0 0 1200 40" aria-hidden="true"><polygon points="0,0 300,0 250,34 0,34" fill="#fff"/></svg>
  <div class="hero-copy">
    <div class="hero-kicker">Welcome To</div>
    <h1 class="hero-title"><span class="accent">Lumora</span><br>Systems</h1>
    <p class="hero-text">Lumora Systems is well experienced in delivering the best in Data Center Infrastructure, Network Infrastructure, Structured Cabling, Telephony, Access Control, Video Surveillance, Audiovisual &amp; Conferencing, Relocation Migration and Maintenance solutions.</p>
  </div>
  <a class="btn outline hero-btn">Get Started
    <svg viewBox="0 0 12 12"><circle cx="6" cy="6" r="6" fill="#fff"/><path d="M4 3.5 6.8 6 4 8.5" stroke="#b3171b" stroke-width="1.6" fill="none"/></svg></a>
  <div class="dots"><i></i><i></i><i></i></div>
  <svg class="hero-edge" width="1200" height="80" viewBox="0 0 1200 80" aria-hidden="true">
    <polygon points="0,69 860,69 1200,10 1200,80 0,80" fill="#fff"/>
    <polyline points="0,63 850,63 1200,2" fill="none" stroke="#b3171b" stroke-width="4"/>
    <polyline points="0,71 862,71 1200,14" fill="none" stroke="#b3171b" stroke-width="2"/>
  </svg>
  <div class="scroll-cue"><svg width="16" height="16" viewBox="0 0 16 16"><circle cx="8" cy="8" r="8" fill="#b3171b"/><path d="M8 4v7M5 8.5 8 11.5 11 8.5" stroke="#fff" stroke-width="1.6" fill="none"/></svg></div>
</section>

<header class="site-header">
  <div class="brand" style="left:66px;top:28px"><span class="brand-square"></span><span class="brand-name">Lumora</span></div>
  <nav class="nav">
    <a class="active" style="left:421px">Home</a>
    <a style="left:508px">About</a>
    <a style="left:592px">Our Services</a>
    <a style="left:720px">Our Projects</a>
    <a style="left:850px">contact Us</a>
  </nav>
  <a class="btn login">Log In
    <svg viewBox="0 0 12 12"><circle cx="6" cy="6" r="6" fill="#fff"/><path d="M4 3.5 6.8 6 4 8.5" stroke="#b3171b" stroke-width="1.6" fill="none"/></svg></a>
</header>

<section class="about">
  <div class="about-photo">
    <div class="frame"></div>
    <div class="shot" role="img" aria-label="Two engineers reviewing a tablet in a data center aisle"></div>
    <span class="sq" style="left:306px;top:68px"></span>
    <span class="sq" style="left:62px;top:310px"></span>
  </div>
  <div class="divider-v"></div>
  <h2 class="about-title">About<br>Lumora Systems</h2>
  <p class="about-text">Lumora Systems is well experienced in delivering the best in Data Center Infrastructure, Network Infrastructure, Structured Cabling, Telephony, Access Control, Video Surveillance, Audiovisual &amp; Conferencing, Relocation &amp; Migration and Maintenance solutions. Our dedication, focus, and expertise wins much recognition of many IT professionals in all industries in the region. In Lumora Systems's Belief, the major reason that we gain a lot of true long-lasting business relationship with our clients was that we offer them the attention, consideration, passion, and professionalism that they deserved.</p>
  <a class="btn outline about-btn">Read More
    <svg viewBox="0 0 12 12"><circle cx="6" cy="6" r="6" fill="#fff"/><path d="M4 3.5 6.8 6 4 8.5" stroke="#b3171b" stroke-width="1.6" fill="none"/></svg></a>
</section>

<section class="services">
  <div class="services-bg"></div>
  <h2 class="section-title">Our Services</h2>
  <article class="svc" style="left:72px" role="img" aria-label="Data center aisle with rows of racks"><h3>Data Center<br>Design And Build</h3></article>
  <article class="svc" style="left:341px" role="img" aria-label="Patch panels with blue network cables"><h3>Structured Cabling<br>And Fiber Backbone</h3></article>
  <article class="svc active" style="left:609px">
    <h3>All-In-One Rack /<br>Micro - Data Center</h3>
    <p>Lumora offers adaptive IT hardware support maintenance service to our customer in order to extend hardware lifecycles and maintain uptime. Our service provides highly skilled technical personnel.</p>
    <a class="btn">Read More
      <svg viewBox="0 0 12 12"><circle cx="6" cy="6" r="6" fill="#b3171b"/><path d="M4 3.5 6.8 6 4 8.5" stroke="#fff" stroke-width="1.6" fill="none"/></svg></a>
  </article>
  <article class="svc" style="left:876px;background:linear-gradient(180deg,#8e99a8,#4b5666)" role="img" aria-label="Empty meeting room with ceiling lights"><h3>Audiovisual and<br>Conference</h3></article>
</section>

<section class="projects">
  <h2>Our Projects</h2>
  <p class="intro">Lorem ipsum dolor sit amet, consectetur adipiscing elit, sed do eiusmod tempor incididunt ut labore et dolore magna aliqua. Quis ipsum suspendisse ultrices gravida.</p>
  <a class="btn outline">Learn More
    <svg viewBox="0 0 12 12"><circle cx="6" cy="6" r="6" fill="#fff"/><path d="M4 3.5 6.8 6 4 8.5" stroke="#b3171b" stroke-width="1.6" fill="none"/></svg></a>
  <article class="proj" style="left:601px;top:6px;width:241px;height:275px" role="img" aria-label="Network rack with blue cabling"><h3>A Renowned China<br>Based Listed Insurance<br>Company</h3></article>
  <article class="proj" style="left:851px;top:6px;width:245px;height:275px;background:linear-gradient(160deg,#3563a6,#18315e)" role="img" aria-label="Dense blue patch cabling"><h3>Orbisfield Trading</h3></article>
  <article class="proj wide" style="left:104px;top:292px;width:491px;height:258px;background:linear-gradient(100deg,#2d5596,#1a2a44 70%,#3a3d45)" role="img" aria-label="Server cabinet fitted with blue cables"><h3>Harbourline Capital &amp; Crestmark Life</h3></article>
  <article class="proj wide" style="left:605px;top:292px;width:491px;height:258px;background:linear-gradient(100deg,#3a3f47,#1f2226 60%,#4a4e55)" role="img" aria-label="Row of dark smart cabinets in a server room"><h3>A Renown China Based Securities Firm</h3></article>
</section>

<section class="partners">
  <h2 class="section-title">Our Partners</h2>
  <div class="badge dark" style="left:-100px"><span></span></div>
  <div class="badge dark" style="left:100px"><span></span></div>
  <div class="badge dark" style="left:301px"><span></span></div>
  <div class="badge focus" style="left:502px"><span></span></div>
  <div class="badge" style="left:705px"><span></span></div>
  <div class="badge dark" style="left:906px"><span></span></div>
  <div class="badge dark" style="left:1107px"><span></span></div>
</section>

<section class="news">
  <div class="news-bg"></div>
  <h2 class="section-title">News And Events</h2>
  <article class="news-card" style="left:116px">
    <div class="thumb" role="img" aria-label="Technician working at a server rack"></div>
    <h3>Lorem Ipsum</h3>
    <div class="meta">
      <span><svg viewBox="0 0 12 12"><rect x="1" y="2" width="10" height="9" rx="1" fill="#222"/><rect x="2" y="5" width="8" height="5" fill="#fff"/></svg>19Dec - 2023</span>
      <span><svg viewBox="0 0 12 12"><circle cx="6" cy="3.5" r="2.5" fill="#222"/><path d="M1 12c0-3 2.2-5 5-5s5 2 5 5z" fill="#222"/></svg>Mara Quill</span>
    </div>
    <p>Lorem ipsum dolor sit amet, consectetur elit, sed do eiusmod tempor incididunt aliqua.</p>
  </article>
  <article class="news-card" style="left:609px">
    <div class="thumb" style="background:linear-gradient(160deg,#5a6270,#1c2028)" role="img" aria-label="Dark cabinet row in a server room"></div>
    <h3>Lorem Ipsum</h3>
    <div class="meta">
      <span><svg viewBox="0 0 12 12"><rect x="1" y="2" width="10" height="9" rx="1" fill="#222"/><rect x="2" y="5" width="8" height="5" fill="#fff"/></svg>19Dec - 2023</span>
      <span><svg viewBox="0 0 12 12"><circle cx="6" cy="3.5" r="2.5" fill="#222"/><path d="M1 12c0-3 2.2-5 5-5s5 2 5 5z" fill="#222"/></svg>Mara Quill</span>
    </div>
    <p>Lorem ipsum dolor sit amet, consectetur elit, sed do eiusmod tempor incididunt aliqua.</p>
  </article>
  <div class="pager"><i></i><i></i></div>
</section>

<section class="blogs">
  <h2 class="section-title">Our Blogs</h2>
  <article class="blog" style="left:104px">
    <div class="cover" style="background:linear-gradient(160deg,#2a2b34,#0f1015 60%,#3a2f4a)" role="img" aria-label="Blog cover with an aisle-containment diagram"></div>
    <h3>Lorem Ipsum</h3>
    <p>Lorem ipsum dolor sit amet, consectetur adipiscing elit, sed do eiusmod tempor incididunt ut labore et dolore magna aliqua.</p>
    <a>Read More</a>
  </article>
  <article class="blog" style="left:442px">
    <div class="cover" style="background:linear-gradient(180deg,#b9c4cc,#7d8b7a 55%,#4f5d48)" role="img" aria-label="Outdoor cabinet in a grassy landscape with a light trail"></div>
    <h3>Lorem Ipsum</h3>
    <p>Lorem ipsum dolor sit amet, consectetur adipiscing elit, sed do eiusmod tempor incididunt ut labore et dolore magna aliqua.</p>
    <a>Read More</a>
  </article>
  <article class="blog" style="left:779px">
    <div class="cover" style="background:linear-gradient(120deg,#1d1f25,#3d4a2f 60%,#6b7a3a)" role="img" aria-label="Blog cover with a cabinet in a forest setting"></div>
    <h3>Lorem Ipsum</h3>
    <p>Lorem ipsum dolor sit amet, consectetur adipiscing elit, sed do eiusmod tempor incididunt ut labore et dolore magna aliqua.</p>
    <a>Read More</a>
  </article>
</section>

<section class="contacts">
  <div class="contacts-bg"></div>
  <h2 class="section-title">Contacts Us</h2>
  <div class="field" style="top:169px">Name</div>
  <div class="field" style="top:233px">Email</div>
  <div class="field" style="top:298px">Phone Number</div>
  <div class="field msg">Messge</div>
  <a class="btn outline">Submit
    <svg viewBox="0 0 12 12"><circle cx="6" cy="6" r="6" fill="#fff"/><path d="M4 3.5 6.8 6 4 8.5" stroke="#b3171b" stroke-width="1.6" fill="none"/></svg></a>
</section>

<footer class="site-footer">
  <div class="brand" style="left:104px;top:38px"><span class="brand-square"></span><span class="brand-name">Lumora</span></div>
  <span class="social" style="left:104px"></span>
  <span class="social" style="left:146px"></span>

  <h4 class="col-title" style="left:349px;top:40px">Quick Links</h4>
  <ul class="links" style="left:351px;top:72px">
    <li class="active">Home</li><li>About</li><li>Our Services</li><li>Our Projects</li><li>Contact Us</li>
  </ul>

  <h4 class="col-title" style="left:514px;top:40px">Services</h4>
  <ul class="links" style="left:515px;top:72px">
    <li>Server Room Design &amp; Build</li><li>All &amp; in &amp; One Rack &amp; Smart Cabinet</li><li>Structured Cabling</li><li>IT Relocation</li><li>Maintenance</li>
  </ul>

  <h4 class="col-title" style="left:798px;top:40px">Contact Us</h4>
  <div class="contact-row" style="top:72px">
    <span class="ic"><svg viewBox="0 0 12 12"><path d="M6 0.5a4 4 0 0 1 4 4c0 3-4 7-4 7s-4-4-4-7a4 4 0 0 1 4-4z" fill="#fff"/><circle cx="6" cy="4.5" r="1.5" fill="#b3171b"/></svg></span>
    <span>Rm 905, 9/F, Brightwater Centre, 18 Kelso Road, Kwun Tong, Kowloon, Hong Kong</span>
  </div>
  <div class="contact-row" style="top:142px">
    <span class="ic"><svg viewBox="0 0 12 12"><rect x="1" y="2.5" width="10" height="7" rx="1" fill="#fff"/><path d="M1.5 3 6 6.5 10.5 3" stroke="#b3171b" fill="none"/></svg></span>
    <span>marketing@lumorasys.com.hk</span>
  </div>
  <div class="contact-row" style="top:180px">
    <span class="ic"><svg viewBox="0 0 12 12"><path d="M3 1l2 2.5-1.2 1.5a7 7 0 0 0 3.2 3.2L8.5 7 11 9l-1.3 2C5 11 1 7 1 2.3z" fill="#fff"/></svg></span>
    <span>+852 2864 1730 / +852 6172 4409</span>
  </div>
  <div class="contact-row" style="top:218px">
    <span class="ic"><svg viewBox="0 0 12 12"><rect x="2" y="3" width="8" height="7" rx="1" fill="#fff"/><rect x="3.5" y="1" width="5" height="3" fill="#fff"/></svg></span>
    <span>+852 3947 0216</span>
  </div>
  <div class="rule"></div>
  <p class="copy">© Copyrights 2023 Lumora Systems | All Rights Reserved</p>
</footer>

</body>
</html>
```